Corwin Beacon Lighting - Commercial & Residential Landscape Lighting

Landscape Lighting Services & Design: Create a website for our landscape lighting company. We would like the design to be tailored around this description:
Illuminate with Confidence. Designed with Precision. Installed with Care.
Locally and veteran-owned, we take pride in transforming outdoor spaces through innovative lighting solutions tailored to your vision. From landscape and holiday lighting to permanent installations, our effortless process and expert design deliver breathtaking results and lasting curb appeal. Backed by a lifetime warranty and quarterly service options, our commitment to quality and customer satisfaction is unwavering. Try before you buy and experience your home in a whole new light with our complimentary demo kit — see the stunning effects before you decide.
- Also, add in this information as well; Outdoor Lighting not only beautifies spaces but also significantly enhances safety by illuminating your home or business. Beautifully lit entrances deter potential intruders, making your home a safer place for your loved ones. we also offer quarterly service plans to ensure lighting equipment continues to operate & illuminate effectively throughout the year. Also mention we provide free estimates and we are offering a 10% discount to military, veterans, and first responders.

Target Market(s)

Luxury market

Industry/Entity Type

Landscape Lighting - Residential & Commercial Lighting Services

Coding

Coded - Design and coding required

Number of Pages Required

2 page

Colors
00AB8E
00BBA5
67D7C9
C6EFE9
E9F9F6
59FF00
82FF00
B8FF75
E3FFCB
F4FFEA
FFC000
F8CF3A
FAE287
FDF2CF
FEFAEE

Requirements
Must have
• a lead generation button where people can submit their information for us to reach out to them and schedule their free estimate, homepage, about page, contact page, products and services page, user friendly, easy to navigate, and it also must be engaging and eye popping, as well as appealing to the luxury market. Please use colors; verdent green, dark green, ivory, and sunny yellow. Also, include an about page that references our story; Derek is retired Army and he opened a fitness studio in 2017 with his wife Jolene. He has installed low voltage lighting in every home he lived in and for his friends and family over the years and decided to open his own business because he is passionate about beautifying outdoor landscapes and highlighting a properties full potential, not only in the day but at night as well all while providing safety and security for his clients. Having a deep respect for nature and landscaping, he wants to provide the same care and quality to each of his clients as he has in the fitness industry for decades. He believes small businesses are the back bone of America and he's excited to provide a service that is all to often neglected in the design of a home.
Nice to have
• I would like to have a clear intent and purpose, engaging web design, clear call to action, optimized for search engines, mobile friendy design, security measures, credibility indicators

```html
<!DOCTYPE html>
<html lang="en">
<head>
<meta charset="utf-8">
<title>Corwin Beacon Lighting – Residential &amp; Commercial Landscape Lighting</title>
<link rel="stylesheet" href="https://fonts.googleapis.com/css2?family=Questrial&family=Montserrat:wght@400;500;600;700&display=swap">
<style>
:root{
  --black:#000;
  --ink:#0a0a0a;
  --gold:#f6b431;
  --gold-deep:#e9a21c;
  --sunny:#ffc000;
  --ivory:#fdf2cf;
  --cream:#fefaee;
  --teal:#00ab8e;
  --teal-lite:#00bba5;
  --mint:#67d7c9;
  --forest:#0e3d2b;
  --forest-2:#154a34;
  --white:#fff;
}
*{box-sizing:border-box;margin:0;padding:0}
html,body{width:1200px;height:4478px;overflow:hidden;background:var(--black)}
body{position:relative;font-family:"Montserrat",sans-serif;color:var(--white)}
.abs{position:absolute}
.display{font-family:"Questrial",sans-serif;text-transform:uppercase;letter-spacing:.02em}
.btn{position:absolute;display:flex;align-items:center;justify-content:center;font-family:"Montserrat",sans-serif;font-weight:700;font-size:13px;letter-spacing:.04em;text-transform:uppercase;text-decoration:none}
.btn-gold{background:var(--gold);color:#1a1200}
.btn-teal{background:linear-gradient(90deg,var(--teal),var(--teal-lite));color:#041a14}
.btn-teal-lite{background:linear-gradient(90deg,var(--teal-lite),var(--mint));color:#041a14}
.btn-ghost{border:2px solid var(--white);color:var(--white)}
.btn-ghost-dark{border:2px solid #1a1200;color:#1a1200}

/* header */
.site-nav{position:absolute;top:0;left:0;width:1200px;height:106px;z-index:5}
.site-nav a{position:absolute;top:60px;font-size:14px;color:var(--white);text-decoration:none;letter-spacing:.04em;text-transform:uppercase}
.site-nav a.active{color:var(--gold)}
.site-nav .underline{position:absolute;left:138px;top:103px;width:48px;height:2px;background:var(--gold)}
.nav-rule{position:absolute;top:104px;height:1px;background:rgba(255,255,255,.2)}
.brand{position:absolute;left:595px;transform:translateX(-50%);text-align:center;color:var(--gold)}
.brand .name{font-family:"Questrial",sans-serif;font-size:44px;letter-spacing:.08em;line-height:1}
.brand .tag{font-family:"Questrial",sans-serif;font-size:12px;letter-spacing:.22em;margin-top:4px}

/* hero */
.hero-photo{position:absolute;left:0;top:0;width:1200px;height:748px;background:
  radial-gradient(ellipse at 50% 30%,rgba(40,35,25,.4),transparent 60%),
  radial-gradient(ellipse at 85% 45%,#7a4a22 0%,#3a2614 25%,transparent 45%),
  radial-gradient(ellipse at 15% 40%,#6a4020 0%,#2c1e12 25%,transparent 45%),
  linear-gradient(180deg,#2a3346 0%,#263040 30%,#1f2418 60%,#2a3a1a 85%,#1c2412 100%)}
.hero-headline{position:absolute;top:225px;left:0;width:1200px;text-align:center;font-size:38px;line-height:50px;font-weight:400}
.hero-headline span{display:block}
.hero-headline .l1{color:var(--ivory)}
.hero-headline .l2{color:var(--gold)}
.hero-headline .l3{color:var(--ivory)}

/* about */
.eyebrow{font-family:"Montserrat",sans-serif;font-size:14px;letter-spacing:.28em;text-transform:uppercase;color:var(--white)}
.section-title{font-family:"Questrial",sans-serif;text-transform:uppercase;color:var(--gold);font-size:38px;line-height:46px;font-weight:400}
.title-rule{height:3px;background:linear-gradient(90deg,var(--gold),rgba(246,180,49,0))}
.about-copy{font-size:15.5px;line-height:27px;color:#e8e8e8}
.about-quote{border-left:2px solid var(--white);padding-left:16px;font-weight:700;font-size:15.5px;line-height:27px}
.promo-card{position:absolute;top:1334px;width:464px;height:137px;display:flex;align-items:center;gap:20px;padding-left:34px}
.promo-card .icon{width:78px;height:78px;border-radius:50%;display:flex;align-items:center;justify-content:center;flex:none}
.promo-card h3{font-family:"Questrial",sans-serif;font-size:21px;font-weight:400;letter-spacing:.02em}
.promo-card p{font-family:"Questrial",sans-serif;font-size:16px;text-transform:uppercase;line-height:20px;margin-top:4px}

/* split */
.split-title{position:absolute;text-align:center;font-size:34px;line-height:39px;font-weight:400}
.split-copy{position:absolute;text-align:center;font-size:16px;line-height:27px}

/* products */
.service-card{position:absolute;top:2256px;height:318px;border:3px solid rgba(255,255,255,.18);overflow:hidden}
.service-card .label{position:absolute;left:0;right:0;bottom:30px;text-align:center;font-weight:700;font-size:21px;line-height:29px;text-transform:uppercase}
.service-card .label .gold{color:var(--gold)}

/* form */
.field{position:absolute;height:47px;background:rgba(0,0,0,.35);border:1px solid rgba(255,255,255,.28);display:flex;align-items:center;gap:10px;padding-left:18px;font-size:14px;color:#e8e8e8}
.field.message{align-items:flex-start;padding-top:18px}

/* footer */
.foot-nav{position:absolute;top:4255px;left:82px;width:996px;height:67px;border-top:1px solid rgba(255,255,255,.25);border-bottom:1px solid rgba(255,255,255,.25);display:flex;align-items:center;justify-content:space-around;padding:0 40px}
.foot-nav a{font-weight:700;font-size:14px;color:var(--white);text-decoration:none;text-transform:uppercase}
.foot-nav .dot{width:4px;height:4px;border-radius:50%;background:var(--gold)}
.contact-item{position:absolute;top:4348px;display:flex;align-items:center;gap:14px;font-size:14px;font-weight:500}
.contact-item .pip{width:36px;height:36px;border-radius:50%;background:var(--gold);display:flex;align-items:center;justify-content:center}
.social{position:absolute;top:4355px;width:24px;height:24px;border-radius:50%;border:2px solid var(--gold)}
.copyright{position:absolute;left:0;top:4426px;width:1200px;height:52px;background:#1c1c1c;display:flex;align-items:center;justify-content:center;font-size:13px;color:#cfcfcf}
</style>
</head>
<body>

<!-- HERO -->
<div class="hero-photo" role="img" aria-label="Brick home at dusk with warm landscape lighting along the lawn and walkway"></div>
<svg class="abs" style="left:0;top:650px" width="1200" height="110" viewBox="0 0 1200 110">
  <path d="M0 98 L600 11 L1200 98 L1200 110 L0 110 Z" fill="#000"/>
  <path d="M0 98 L600 11 L1200 98" fill="none" stroke="#f6b431" stroke-width="3"/>
</svg>

<header class="site-nav">
  <div class="nav-rule" style="left:120px;width:340px"></div>
  <div class="nav-rule" style="left:730px;width:260px"></div>
  <a class="active" href="#" style="left:138px">Home</a>
  <span class="underline"></span>
  <a href="#" style="left:235px">About</a>
  <a href="#" style="left:337px">Services</a>
  <div class="brand" style="top:26px"><div class="name">CORWIN</div><div class="tag">BEACON LIGHTING</div></div>
  <a href="#" style="left:750px">Products</a>
  <a href="#" style="left:882px">Contact Us</a>
  <a class="btn btn-gold" href="#" style="left:1016px;top:47px;width:154px;height:40px;font-size:12px">Free Estimate ›</a>
</header>

<h1 class="hero-headline display">
  <span class="l1">Illuminate with Confidence.</span>
  <span class="l2">Designed with Precision.</span>
  <span class="l3">Installed with Care.</span>
</h1>
<a class="btn btn-teal" href="#" style="left:514px;top:403px;width:180px;height:44px">Free Estimate ›</a>

<!-- ABOUT -->
<svg class="abs" style="left:150px;top:860px" width="420" height="420" viewBox="0 0 420 420">
  <path d="M212 16 A196 196 0 1 0 360 84" fill="none" stroke="#fdf2cf" stroke-width="14" stroke-linecap="round"/>
</svg>
<div class="abs" role="img" aria-label="Two-storey home among tall pines with glowing landscape lights at sunset" style="left:175px;top:886px;width:374px;height:374px;border-radius:50%;background:radial-gradient(circle at 50% 60%,#b07a34 0%,#6b5a2a 35%,#3f4a22 65%,#2a3418 100%)"></div>

<div class="abs eyebrow" style="left:618px;top:780px">Who We Are</div>
<h2 class="abs section-title" style="left:614px;top:803px">About Corwin<br>Beacon Lighting</h2>
<div class="abs title-rule" style="left:616px;top:900px;width:200px"></div>
<p class="abs about-copy" style="left:616px;top:924px;width:548px">Locally and veteran-owned, we take pride in transforming outdoor spaces through innovative lighting solutions tailored to your vision. From landscape and holiday lighting to permanent installations, our effortless process and expert design deliver breathtaking results and lasting curb appeal. Backed by a lifetime warranty and quarterly service options, our commitment to quality and customer satisfaction is unwavering.</p>
<p class="abs about-quote" style="left:620px;top:1134px;width:520px">Try before you buy and experience your home in a whole new light with our complimentary demo kit — see the stunning effects before you decide.</p>
<a class="btn btn-gold" href="#" style="left:621px;top:1240px;width:180px;height:44px">Learn More ›</a>

<div class="promo-card" style="left:122px;border:2px solid var(--teal)">
  <div class="icon" style="background:var(--teal)">
    <svg width="38" height="38" viewBox="0 0 38 38" fill="none" stroke="#fff" stroke-width="2"><rect x="8" y="5" width="22" height="28" rx="2"/><path d="M13 13h12M13 19h12M13 25h7"/></svg>
  </div>
  <div><h3>WE PROVIDE FREE ESTIMATE</h3><p>Get a free estimate now</p></div>
</div>
<div class="promo-card" style="left:614px;border:2px solid var(--gold-deep)">
  <div class="icon" style="background:var(--gold)">
    <svg width="38" height="38" viewBox="0 0 38 38" fill="none" stroke="#1a1200" stroke-width="2"><path d="M13 4h12l-3 10h-6z"/><circle cx="19" cy="24" r="9"/><path d="M19 19l1.6 3.4 3.6.4-2.7 2.4.8 3.6L19 27l-3.3 1.8.8-3.6-2.7-2.4 3.6-.4z"/></svg>
  </div>
  <div><h3>WE OFFERING A 10% DISCOUNT</h3><p>To military, veterans, and<br>first responders</p></div>
</div>

<!-- RESIDENTIAL / COMMERCIAL SPLIT -->
<svg class="abs" style="left:0;top:1534px" width="1200" height="550" viewBox="0 0 1200 550" role="img" aria-label="Garden stone steps and a commercial building softly lit, tinted green and gold">
  <defs>
    <linearGradient id="tealPanel" x1="0" y1="0" x2="1" y2="1"><stop offset="0" stop-color="#1a8a6a"/><stop offset=".5" stop-color="#11a384"/><stop offset="1" stop-color="#0b7d62"/></linearGradient>
    <linearGradient id="goldPanel" x1="0" y1="0" x2="1" y2="1"><stop offset="0" stop-color="#f6b61e"/><stop offset=".6" stop-color="#f8c640"/><stop offset="1" stop-color="#f1b040"/></linearGradient>
  </defs>
  <path d="M0 0 L600 63 L600 487 L0 550 Z" fill="url(#tealPanel)"/>
  <path d="M600 63 L1200 0 L1200 550 L600 487 Z" fill="url(#goldPanel)"/>
</svg>
<h2 class="split-title display" style="left:0;top:1684px;width:640px;color:var(--white)">Residential<br>Landscape Lighting</h2>
<div class="abs" style="left:200px;top:1780px;width:240px;height:2px;background:linear-gradient(90deg,transparent,#fff,transparent)"></div>
<p class="split-copy" style="left:90px;top:1798px;width:460px">Lorem ipsum dolor sit amet, consectetur adipiscing elit, sed do eiusmod tempor incididun</p>
<a class="btn btn-ghost" href="#" style="left:230px;top:1874px;width:180px;height:44px">Learn More ›</a>

<h2 class="split-title display" style="left:600px;top:1684px;width:600px;color:#1a1200">Commercial<br>Landscape Lighting</h2>
<div class="abs" style="left:780px;top:1780px;width:240px;height:2px;background:linear-gradient(90deg,transparent,#1a1200,transparent)"></div>
<p class="split-copy" style="left:670px;top:1798px;width:460px;color:#1a1200">Lorem ipsum dolor sit amet, consectetur adipiscing elit, sed do eiusmod tempor incididun</p>
<a class="btn btn-ghost-dark" href="#" style="left:818px;top:1872px;width:182px;height:44px">Learn More ›</a>

<!-- PRODUCTS & SERVICES -->
<div class="abs" role="img" aria-label="Large home at night with warmly lit windows and terrace" style="left:0;top:2200px;width:1200px;height:690px;background:
  radial-gradient(ellipse at 60% 75%,#8a5a1e 0%,#4a3214 25%,transparent 50%),
  radial-gradient(ellipse at 20% 70%,#3a2a14 0%,transparent 40%),
  linear-gradient(180deg,#000 0%,#0a0c10 20%,#141a20 55%,#10140c 85%,#000 100%)"></div>
<div class="abs eyebrow" style="left:0;top:2114px;width:1200px;text-align:center">What We Do</div>
<h2 class="abs section-title" style="left:0;top:2134px;width:1200px;text-align:center">Products &amp; Services</h2>
<div class="abs" style="left:465px;top:2190px;width:270px;height:3px;background:linear-gradient(90deg,transparent,var(--gold),transparent)"></div>

<div class="service-card" style="left:129px;width:302px;background:linear-gradient(180deg,#2c3a22 0%,#3f5a2a 45%,#5a6a2a 75%,#2a2a14 100%)" role="img" aria-label="Garden path with bollard light and lush planting">
  <div class="label"><span class="gold">Landscape</span><br>Lighting</div>
</div>
<div class="service-card" style="left:461px;width:299px;background:linear-gradient(180deg,#0f4a30,#0c3a26);border-color:rgba(0,171,142,.45)">
  <div class="abs" style="left:0;top:44px;width:293px;text-align:center;font-weight:700;font-size:21px;line-height:29px;text-transform:uppercase"><span style="color:var(--gold)">Holiday</span><br>Lighting</div>
  <p class="abs" style="left:42px;top:112px;width:210px;text-align:center;font-size:12px;line-height:19px;color:#e8e8e8">Lorem ipsum dolor sit amet, consectetur adipiscing elit, sed do eiusmod tempor incididunt ut labore et dolore magna aliqua. Quis ipsum suspendisse ultrice</p>
  <a class="btn btn-gold" href="#" style="left:88px;top:225px;width:118px;height:33px;font-size:11px">Learn More ›</a>
</div>
<div class="service-card" style="left:786px;width:303px;background:linear-gradient(180deg,#4a5e84 0%,#33405a 35%,#5a4426 65%,#1e1a14 100%)" role="img" aria-label="Stone house facade with permanent uplighting at dusk">
  <div class="label"><span class="gold">Permanent</span><br>Installations</div>
</div>

<!-- WHY OUTDOOR LIGHTING -->
<div class="abs eyebrow" style="left:140px;top:2918px">Outdoor Lighting</div>
<h2 class="abs section-title" style="left:138px;top:2940px">Why Outdoor<br>Lighting</h2>
<div class="abs title-rule" style="left:140px;top:3037px;width:180px"></div>
<div class="abs about-copy" style="left:136px;top:3064px;width:500px;font-size:18px;line-height:27px">
  <p>Outdoor Lighting not only beautifies spaces but also significantly enhances safety by illuminating your home or business.</p>
  <p style="margin-top:12px">Beautifully lit entrances deter potential intruders, making your home a safer place for your loved ones. we also offer quarterly service plans to ensure lighting equipment continues to operate &amp; illuminate effectively throughout the year.</p>
</div>
<a class="btn btn-teal-lite" href="#" style="left:137px;top:3336px;width:180px;height:44px">Free Estimate ›</a>
<svg class="abs" style="left:678px;top:2900px" width="522" height="498" viewBox="0 0 522 498" role="img" aria-label="Brick home with arched window and lit shrubs across a wide lawn">
  <defs><linearGradient id="whyPhoto" x1="0" y1="0" x2="0" y2="1"><stop offset="0" stop-color="#3c4660"/><stop offset=".35" stop-color="#56443a"/><stop offset=".6" stop-color="#7a5a30"/><stop offset="1" stop-color="#5a6a3a"/></linearGradient></defs>
  <path d="M170 0 L522 0 L522 498 L170 498 C40 430 -20 290 20 170 C45 90 100 30 170 0 Z" fill="url(#whyPhoto)"/>
</svg>

<!-- CONTACT / ESTIMATE FORM -->
<div class="abs" role="img" aria-label="Evening garden with glowing bollard light beside a lawn" style="left:0;top:3478px;width:1200px;height:660px;background:
  radial-gradient(ellipse at 8% 45%,#c89a40 0%,#4a3a1a 12%,transparent 30%),
  linear-gradient(180deg,#000 0%,#0f1e18 25%,#14281c 60%,#0a120c 90%,#000 100%)"></div>
<div class="abs" style="left:132px;top:3534px;width:945px;height:558px;border-radius:18px;border:1px solid rgba(0,171,142,.45);background:linear-gradient(160deg,rgba(20,82,56,.95),rgba(12,56,38,.95))"></div>
<div class="abs eyebrow" style="left:0;top:3614px;width:1200px;text-align:center;color:var(--gold);font-size:15px">Contact Us</div>
<h2 class="abs section-title" style="left:0;top:3636px;width:1200px;text-align:center;color:var(--ivory);font-size:36px">Schedule Free Estimate</h2>
<div class="abs" style="left:460px;top:3684px;width:280px;height:3px;background:linear-gradient(90deg,transparent,var(--gold),transparent)"></div>

<div class="field" style="left:234px;top:3716px;width:360px"><svg width="13" height="13" viewBox="0 0 14 14" fill="#e8e8e8"><circle cx="7" cy="4" r="3.2"/><path d="M1 14c0-4 3-6 6-6s6 2 6 6z"/></svg>First Name</div>
<div class="field" style="left:605px;top:3716px;width:362px"><svg width="13" height="13" viewBox="0 0 14 14" fill="#e8e8e8"><circle cx="7" cy="4" r="3.2"/><path d="M1 14c0-4 3-6 6-6s6 2 6 6z"/></svg>Last Name</div>
<div class="field" style="left:234px;top:3778px;width:360px"><svg width="14" height="11" viewBox="0 0 14 11" fill="#e8e8e8"><path d="M0 0h14v1.6L7 6 0 1.6z"/><path d="M0 3.4l7 4.4 7-4.4V11H0z"/></svg>Email address</div>
<div class="field" style="left:605px;top:3778px;width:362px"><svg width="13" height="13" viewBox="0 0 14 14" fill="#e8e8e8"><path d="M3 0l3 3-2 2c1 2 3 4 5 5l2-2 3 3-2 3C6 14 0 8 0 2z"/></svg>Phone number</div>
<div class="field message" style="left:234px;top:3840px;width:733px;height:117px"><svg width="13" height="12" viewBox="0 0 14 13" fill="#e8e8e8"><path d="M7 0C3 0 0 2.4 0 5.5c0 1.6.8 3 2.2 4L1.5 13l3.6-2.2c.6.1 1.2.2 1.9.2 4 0 7-2.5 7-5.5S11 0 7 0z"/></svg>Leave Message</div>
<a class="btn btn-gold" href="#" style="left:495px;top:3982px;width:210px;height:47px;font-size:15px">Send Message ›</a>

<!-- FOOTER -->
<div class="brand" style="top:4150px;left:600px"><div class="name">CORWIN</div><div class="tag">BEACON LIGHTING</div></div>

<nav class="foot-nav">
  <a href="#">Home</a><span class="dot"></span>
  <a href="#">About Us</a><span class="dot"></span>
  <a href="#">Services</a><span class="dot"></span>
  <a href="#">Products</a><span class="dot"></span>
  <a href="#">Gallery</a><span class="dot"></span>
  <a href="#">Contact</a>
</nav>

<div class="contact-item" style="left:176px">
  <span class="pip"><svg width="14" height="18" viewBox="0 0 14 18" fill="#1a1200"><path d="M7 0a7 7 0 0 0-7 7c0 5 7 11 7 11s7-6 7-11a7 7 0 0 0-7-7zm0 9.5A2.5 2.5 0 1 1 7 4.5a2.5 2.5 0 0 1 0 5z"/></svg></span>123 Street Address line
</div>
<div class="contact-item" style="left:456px">
  <span class="pip"><svg width="16" height="16" viewBox="0 0 14 14" fill="#1a1200"><path d="M3 0l3 3-2 2c1 2 3 4 5 5l2-2 3 3-2 3C6 14 0 8 0 2z"/></svg></span>(555) 014-2290
</div>
<div class="contact-item" style="left:658px">
  <span class="pip"><svg width="16" height="12" viewBox="0 0 14 11" fill="#1a1200"><path d="M0 0h14v1.6L7 6 0 1.6z"/><path d="M0 3.4l7 4.4 7-4.4V11H0z"/></svg></span>enquiry@corwinbeacon.com
</div>
<span class="social" style="left:916px"></span>
<span class="social" style="left:955px"></span>
<span class="social" style="left:993px"></span>
<span class="social" style="left:1032px"></span>

<div class="copyright">Copyright © 2025 Corwin Beacon Lighting &nbsp;|&nbsp; All Right Reserved</div>

</body>
</html>
```